Letterhead for Conveyancing Company

Use existing logo to create a letterhead for a conveyancing company. Must be able to be used in Microsoft Word. Easy to read and professional.
Contact information to be at the bottom.
Bright Oak Conveyancing Pty Ltd
ACN 621 984 736PO Box 535 Campbelltown SA 5074
Mobile - 0461739286
Web address - www.brightoakconveyancing.com.au

Requirements
Must have
• Logo and contact details.
• Simple and professional.

```html
<!DOCTYPE html>
<html lang="en">
<head>
<meta charset="utf-8">
<title>Bright Oak Conveyancing – Letterhead</title>
<link rel="stylesheet" href="https://fonts.googleapis.com/css2?family=Roboto:wght@400;500;700&family=Great+Vibes&display=swap">
<style>
  :root {
    --backdrop: #4e4b4a;
    --paper: #fafafa;
    --ink: #5f5f5f;
    --ink-dark: #444444;
    --brand-pink: #e1449a;
    --brand-grey: #7d7d7d;
    --watermark: #efefef;
    --white: #ffffff;
  }
  * { margin: 0; padding: 0; box-sizing: border-box; }
  html, body {
    width: 1062px; height: 1200px; overflow: hidden;
    background: var(--backdrop);
    font-family: "Roboto", Arial, sans-serif;
  }
  .letterhead {
    position: absolute; left: 120px; top: 18px;
    width: 822px; height: 1163px;
    background: var(--paper);
    overflow: hidden;
    color: var(--ink);
    font-size: 13px;
  }
  .brand-name {
    position: absolute; right: 52px; top: 60px;
    text-align: right;
    color: var(--brand-grey);
    font-weight: 700;
    font-size: 44px; line-height: 46px;
    letter-spacing: -0.5px;
  }
  .brand-name .dot {
    display: inline-block; width: 12px; height: 12px;
    background: var(--brand-pink); border-radius: 50%;
    margin-left: 6px; vertical-align: middle;
  }
  .watermark {
    position: absolute; left: 110px; top: 390px;
    width: 600px;
    color: var(--watermark);
    font-weight: 700;
    font-size: 150px; line-height: 140px;
    text-align: center;
    pointer-events: none;
  }
  .letter-body { position: absolute; left: 51px; top: 284px; width: 719px; }
  .date { line-height: 18px; }
  .recipient { margin-top: 38px; line-height: 18.6px; }
  .recipient strong { color: var(--ink-dark); font-weight: 500; }
  .salutation { margin-top: 37px; }
  .letter-body p.copy {
    margin-top: 19px;
    line-height: 18.6px;
    text-align: justify;
  }
  .sign-off { position: absolute; left: 51px; top: 918px; }
  .sign-off .signer { color: var(--ink-dark); font-weight: 500; }
  .sign-off .signature {
    font-family: "Great Vibes", cursive;
    font-size: 38px; color: #3a4a6a;
    margin: 2px 0 0 -18px; line-height: 44px;
  }
  .sign-off .role { margin-top: 4px; }
  .company-name {
    position: absolute; left: 43px; top: 1050px;
    color: var(--brand-pink);
    font-size: 19px; font-weight: 500;
  }
  .footer-band { position: absolute; left: 0; top: 1088px; width: 822px; height: 75px; }
  .contact {
    position: absolute; left: 44px; top: 1102px;
    color: var(--white); font-size: 15.5px;
  }
  .contact-row { display: flex; align-items: center; height: 24px; }
  .contact-row svg { width: 15px; height: 15px; margin-right: 12px; }
  .contact-row .web { margin-left: 14px; display: flex; align-items: center; }
  .acn {
    position: absolute; right: 52px; top: 1128px;
    color: var(--white); font-size: 15.5px;
  }
</style>
</head>
<body>
<main class="letterhead">
  <div class="brand-name">Bright<br>Oak<span class="dot"></span></div>

  <div class="watermark" aria-hidden="true">Bright Oak</div>

  <section class="letter-body">
    <div class="date">30/20/2016</div>
    <address class="recipient" style="font-style:normal">
      <strong>Mr. XYZ Smith</strong><br>
      123, Street No. 123,<br>
      City Name<br>
      Pincode-123456
    </address>
    <div class="salutation">Dear Sir,</div>
    <p class="copy">Lorem Ipsum is simply dummy text of the printing and typesetting industry. Lorem Ipsum has been the industry's standard dummy text ever since the 1500s, when an unknown printer took a galley of type and scrambled it to make a type specimen book. It has survived not only five centuries, but also the leap into electronic typesetting, remaining essentially unchanged. It was popularised in the 1960s with the release of Letraset sheets containing Lorem Ipsum passages, and more recently with desktop publishing software like Aldus PageMaker including versions of Lorem Ipsum.</p>
    <p class="copy">Lorem Ipsum is simply dummy text of the printing and typesetting industry. Lorem Ipsum has been the industry's standard dummy text ever since the 1500s, when an unknown printer took a galley of type and scrambled it to make a type specimen book. It has survived not only five centuries, but also the leap into electronic typesetting, remaining essentially unchanged. It was popularised in the 1960s with the release of Letraset sheets containing Lorem Ipsum passages, and more recently with desktop publishing software like Aldus PageMaker including versions of Lorem Ipsum.</p>
    <p class="copy">Lorem Ipsum is simply dummy text of the printing and typesetting industry. Lorem Ipsum has been the industry's standard dummy text ever since the 1500s, when an unknown printer took a galley of type and scrambled it to make a type specimen book.</p>
    <p class="copy">Lorem Ipsum is simply dummy text of the printing and typesetting industry. Lorem Ipsum has been the industry's standard dummy text ever since the 1500s, when an unknown printer took a galley of type and scrambled it to make a type specimen book.</p>
  </section>

  <section class="sign-off">
    <div class="signer">Your Name</div>
    <div class="signature">Your Signature</div>
    <div class="role">CEO &nbsp;|&nbsp; Owner</div>
  </section>

  <div class="company-name">Bright Oak Conveyancing Pty Ltd</div>

  <svg class="footer-band" viewBox="0 0 822 75" aria-hidden="true">
    <polygon points="576,24 822,24 822,75 536,75" fill="var(--brand-grey)"/>
    <polygon points="0,0 668,0 536,75 0,75" fill="var(--brand-pink)"/>
  </svg>

  <div class="contact">
    <div class="contact-row">
      <svg viewBox="0 0 16 16" aria-hidden="true"><path d="M8 1a5 5 0 0 0-5 5c0 3.6 5 9 5 9s5-5.4 5-9a5 5 0 0 0-5-5zm0 7a2 2 0 1 1 0-4 2 2 0 0 1 0 4z" fill="var(--white)"/></svg>
      PO Box 871 Marlowdale SA 5096
    </div>
    <div class="contact-row">
      <svg viewBox="0 0 16 16" aria-hidden="true"><path d="M2 6c0-2 3-3.5 6-3.5S14 4 14 6l-3 .5-.5-1.5h-5L5 6.5zM4 8h8l1.5 5h-11z" fill="var(--white)"/></svg>
      046 173 9286
      <span class="web">
        <svg viewBox="0 0 16 16" aria-hidden="true"><circle cx="8" cy="8" r="6.5" fill="none" stroke="var(--white)" stroke-width="1.4"/><path d="M1.5 8h13M8 1.5c-3 3.5-3 9.5 0 13M8 1.5c3 3.5 3 9.5 0 13" fill="none" stroke="var(--white)" stroke-width="1.2"/></svg>
        www.brightoakconveyancing.com.au
      </span>
    </div>
  </div>

  <div class="acn">ACN 583 217 469</div>
</main>
</body>
</html>
```